Casino with the 'highest winning percentage' needs a stationery design

This is for a casino in Colombo, Sri Lanka and we need a stationery design for business card, letter head and envelope.

Should be very professional, simple and elegant without fancy fonts

Reason: Not fully satisfied with the designs. Need more designs.

Business

• 1. card deck symbol 'CLUBS' in red, or black

2. name in BLOCK CAPITAL LETTERS

3. Preferred font colours are black, white or red

4. Prefer 'professional /elegant' fonts
• SHOULD NOT HAVE ANY OTHER SYMBOL EXCEPT 'CLUBS'

DO NOT PREFER ITALIC FONTS

```html
<!DOCTYPE html>
<html lang="en">
<head>
<meta charset="utf-8">
<title>Marlow's Entertainment – Business Card</title>
<link rel="stylesheet" href="https://fonts.googleapis.com/css2?family=Merriweather:wght@400;700&display=swap">
<style>
  :root {
    --page: #e9e6e1;
    --card-light: #c9cacc;
    --card-dark: #a7a8ab;
    --ink: #1c1c1c;
    --red: #dc3040;
    --black: #141414;
    --white: #ffffff;
  }
  * { box-sizing: border-box; margin: 0; padding: 0; }
  html, body {
    width: 1200px; height: 1057px; overflow: hidden;
    background: var(--page);
    font-family: "Merriweather", Georgia, serif;
    color: var(--ink);
  }
  .card {
    position: absolute;
    width: 760px; height: 430px;
    background: radial-gradient(ellipse at 40% 35%, var(--card-light) 0%, var(--card-dark) 100%);
    box-shadow: 0 6px 18px rgba(0,0,0,.18);
    overflow: hidden;
  }
  .card-front { left: 60px; top: 50px; }
  .card-back { left: 380px; top: 570px; }

  .swoosh { position: absolute; inset: 0; width: 100%; height: 100%; }

  .brand { position: absolute; display: flex; align-items: center; gap: 26px; }
  .brand-dot { width: 84px; height: 84px; border-radius: 50%; background: var(--red); flex: none; }
  .brand-name {
    font-weight: 700; font-size: 38px; line-height: 1.12;
    letter-spacing: 1px; text-transform: uppercase; color: var(--ink);
  }
  .card-front .brand { left: 58px; top: 62px; }

  .contacts { position: absolute; left: 70px; top: 196px; list-style: none; }
  .contacts li {
    display: flex; align-items: center; gap: 12px;
    font-size: 17px; line-height: 25px; color: var(--ink);
  }
  .contacts svg { width: 15px; height: 15px; fill: var(--red); flex: none; }

  .address {
    position: absolute; right: 28px; bottom: 26px;
    text-align: right; color: var(--white);
    font-size: 15px; line-height: 1.45; font-style: normal;
  }
  .address .company { font-weight: 700; font-size: 16px; text-transform: uppercase; }

  .card-back .brand { left: 70px; top: 96px; }
  .card-back .brand-dot { width: 110px; height: 110px; }
  .card-back .brand-name { font-size: 44px; }
  .tagline {
    position: absolute; left: 0; right: 0; top: 268px; text-align: center;
    color: var(--red); font-weight: 700; font-size: 27px; letter-spacing: 2.5px;
  }
  .web {
    position: absolute; left: 0; right: 0; top: 330px; text-align: center;
    color: var(--ink); font-size: 22px; letter-spacing: 6px;
  }
</style>
</head>
<body>

<section class="card card-front" aria-label="Business card front">
  <svg class="swoosh" viewBox="0 0 760 430" preserveAspectRatio="none" aria-hidden="true">
    <path fill="var(--red)" d="M0,392 C450,392 660,258 745,0 L758,0 C672,266 458,402 0,401 Z"/>
    <path fill="var(--black)" d="M0,407 C455,405 675,272 760,14 L760,36 C684,294 462,418 0,421 Z"/>
    <path fill="var(--red)" d="M0,430 C460,425 690,292 760,46 L760,430 Z"/>
  </svg>

  <div class="brand">
    <span class="brand-dot"></span>
    <p class="brand-name">Marlow's<br>Entertainment</p>
  </div>

  <ul class="contacts">
    <li><svg viewBox="0 0 16 16"><path d="M3 1h3l1 4-2 1a9 9 0 0 0 5 5l1-2 4 1v3c0 1-1 2-2 2A13 13 0 0 1 1 3c0-1 1-2 2-2z"/></svg>+94 11 2480375</li>
    <li><svg viewBox="0 0 16 16"><path d="M4 0h8a1 1 0 0 1 1 1v14a1 1 0 0 1-1 1H4a1 1 0 0 1-1-1V1a1 1 0 0 1 1-1zm1 2v9h6V2zm3 10.5a1 1 0 1 0 0 2 1 1 0 0 0 0-2z"/></svg>+94 77 5550142</li>
    <li><svg viewBox="0 0 16 16"><path d="M4 1h7v4H4zM2 6h12a1 1 0 0 1 1 1v6a1 1 0 0 1-1 1H2a1 1 0 0 1-1-1V7a1 1 0 0 1 1-1zm2 3v2h5V9z"/></svg>+94 11 5550186</li>
    <li><svg viewBox="0 0 16 16"><path d="M1 3h14v10H1zm1.5 1.5V5l5.5 4 5.5-4v-.5z"/></svg>info@marlowscolombo.com</li>
    <li><svg viewBox="0 0 16 16"><path d="M8 1a7 7 0 1 0 0 14A7 7 0 0 0 8 1zm-1 2v4H3.2A5 5 0 0 1 7 3zm2 0a5 5 0 0 1 3.8 4H9zM3.2 9H7v4a5 5 0 0 1-3.8-4zM9 9h3.8A5 5 0 0 1 9 13z"/></svg>www.marlowscolombo.com</li>
  </ul>

  <address class="address">
    <p class="company">Marlow's Limited</p>
    <p>18, Lotus Garden Road,</p>
    <p>Colombo 00300, Sri Lanka</p>
  </address>
</section>

<section class="card card-back" aria-label="Business card back">
  <div class="brand">
    <span class="brand-dot"></span>
    <p class="brand-name">Marlow's<br>Entertainment</p>
  </div>
  <p class="tagline">Highest Winning Percentage In The World</p>
  <p class="web">www.marlowscolombo.com</p>
</section>

</body>
</html>
```